Plumbing company needs Business Card Design

Hi I need business card design based on logo which I uploaded. Its plumbing and heating company called Kranex Usługi Hydrauliczno-Gazowe. I want to see on my card motto of my company which is "...od wymiany uszczelki po wymiane łazienki.", my phone number, name, and website: 612478390, Marek Olejnik, info@kranex-inst.org, www.kranex-inst.org
I want to see logos of companys which I'm approved installer (Termova) (Le Valmont) (Korvo) (Plumox).
I want new creative look of business card. I like rounded corners.
Any questions please send message.
Thanks for intrest.
Industry/Entity Type
Business
Contact Information for Business Card
Marek Olejnik
612 478 390
info@kranex-inst.org
www.kranex-inst.org
...od wymiany uszczelki po wymiane łazienki.

```html
<!DOCTYPE html>
<html lang="pl">
<head>
<meta charset="utf-8">
<title>Kranex – wizytówka</title>
<link rel="stylesheet" href="https://fonts.googleapis.com/css2?family=Roboto+Condensed:ital,wght@0,400;0,700;0,900;1,700;1,900&display=swap">
<style>
  :root {
    --bg: #e9e6e1;
    --yellow: #f2ea2a;
    --yellow-light: #f7f3a0;
    --red: #e52230;
    --blue: #2a4a9c;
    --white: #ffffff;
    --ink: #1b1b1b;
    --grey-blue: #6f8fbf;
  }
  * { box-sizing: border-box; margin: 0; padding: 0; }
  html, body { width: 1200px; height: 858px; overflow: hidden; }
  body {
    background: var(--bg);
    font-family: "Roboto Condensed", "Arial Narrow", sans-serif;
    display: flex;
    align-items: center;
    justify-content: center;
    gap: 70px;
  }
  .card {
    position: relative;
    border-radius: 24px;
    overflow: hidden;
    box-shadow: 0 10px 30px rgba(0,0,0,.18);
  }
  .card-bg { position: absolute; inset: 0; width: 100%; height: 100%; }

  /* front */
  .card-front { width: 380px; height: 620px; }
  .front-content {
    position: absolute; inset: 0;
    padding: 60px 28px 0 40px;
  }
  .brand { display: flex; align-items: center; gap: 12px; }
  .brand-dot { width: 26px; height: 26px; background: var(--blue); border-radius: 50%; flex: none; }
  .brand-name { font-weight: 900; font-size: 62px; line-height: 1; color: var(--red); }
  .brand-tagline { margin: 6px 0 0 38px; font-size: 18px; color: var(--blue); }
  .motto { margin-top: 12px; font-size: 14px; font-weight: 700; font-style: italic; color: var(--blue); }
  .person { margin-top: 30px; font-size: 32px; font-weight: 900; font-style: italic; color: var(--blue); }
  .contact { margin-top: 28px; list-style: none; font-weight: 900; font-style: italic; color: var(--red); line-height: 1.15; }
  .contact .phone { font-size: 36px; }
  .contact .email { font-size: 27px; }
  .contact .web { font-size: 27px; }
  .partners {
    margin-top: 44px;
    display: grid; grid-template-columns: auto auto; gap: 18px 26px;
    align-items: center; justify-content: start;
  }
  .partner { display: flex; align-items: center; gap: 6px; font-weight: 700; font-size: 22px; line-height: 1; }
  .partner-termova { color: var(--ink); }
  .partner-korvo { color: var(--grey-blue); }
  .partner-valmont { color: var(--ink); font-size: 30px; font-weight: 400; }
  .partner-plumox { color: var(--ink); }
  .partner-mark { width: 14px; height: 14px; background: var(--blue); flex: none; }
  .partner-plumox .partner-mark { background: var(--yellow); }

  /* back */
  .card-back { width: 620px; height: 380px; }
  .back-content { position: absolute; left: 56px; top: 66px; }
  .back-name { font-weight: 900; font-size: 170px; line-height: .9; color: var(--red); }
  .back-tagline { margin-top: 18px; font-size: 38px; color: var(--blue); }
</style>
</head>
<body>

  <article class="card card-front">
    <svg class="card-bg" viewBox="0 0 380 620" preserveAspectRatio="none" aria-hidden="true">
      <rect width="380" height="620" fill="var(--yellow)"/>
      <ellipse cx="175" cy="310" rx="250" ry="370" transform="rotate(-10 175 310)" fill="var(--white)" stroke="var(--blue)" stroke-width="5"/>
    </svg>
    <div class="front-content">
      <header class="brand">
        <span class="brand-dot"></span>
        <span class="brand-name">Kranex</span>
      </header>
      <p class="brand-tagline">Usługi Hydrauliczno-Gazowe</p>
      <p class="motto">...od wymiany uszczelki po wymiane łazienki.</p>
      <h1 class="person">Marek Olejnik</h1>
      <ul class="contact">
        <li class="phone">612 478 390</li>
        <li class="email">info@kranex-inst.org</li>
        <li class="web">www.kranex-inst.org</li>
      </ul>
      <div class="partners">
        <span class="partner partner-termova"><span class="partner-mark"></span>TERMOVA</span>
        <span class="partner partner-korvo">KORVO</span>
        <span class="partner partner-valmont">Le Valmont</span>
        <span class="partner partner-plumox"><span class="partner-mark"></span>plumox</span>
      </div>
    </div>
  </article>

  <article class="card card-back">
    <svg class="card-bg" viewBox="0 0 620 380" preserveAspectRatio="none" aria-hidden="true">
      <defs>
        <radialGradient id="backGlow" cx="40%" cy="45%" r="70%">
          <stop offset="0" stop-color="var(--yellow-light)"/>
          <stop offset="1" stop-color="var(--yellow)"/>
        </radialGradient>
      </defs>
      <rect width="620" height="380" fill="var(--red)"/>
      <ellipse cx="230" cy="150" rx="420" ry="320" fill="var(--blue)"/>
      <ellipse cx="226" cy="146" rx="414" ry="314" fill="url(#backGlow)"/>
    </svg>
    <div class="back-content">
      <p class="back-name">Kranex</p>
      <p class="back-tagline">Usługi Hydrauliczno-Gazowe</p>
    </div>
  </article>

</body>
</html>
```